Corporate Travel Technology Company needs new Business Card design

We need a new business card design to reflect our re-branded company. Our company is called tolvEn (pronounced tolvenn) and we provide Business Intelligence and mobile travel management solutions for the corporate travel industry. Our multinational customers use our solutions to manage large travel budgets and frequent travellers, as well as to save money and reduce risk. We'd like to see designs that use the blue and green palette as well as our corporate logo (attached below). The design should communicate innovation, insight, forward thinking, contemporary, trusted.

Target Market(s)

Large multinational corporates and Travel Agencies.

Industry/Entity Type

Business

Contact Information for Business Card

Rosalind Mercer
Chief Executive
tolvEn
Phone number - +61 (0)2 8134 2907
Email address - rosalind.mercer@tolven-example.com
Mobile number - +61 (0)438 516 702
www.tolven-example.com

Font styles to use
Other font styles liked:
• Please use font as close to corporate logo as possible

Colors
0255a3
0393ce
00a990
33b8a4
33a6d7
3176b5

Requirements
Must have
• Please include the words;
• Mobile Travel Management
• Accelerating Travel Business Insights
• Use corporate logo - although icon can be stylised if needed

```html
<!DOCTYPE html>
<html lang="en">
<head>
<meta charset="utf-8">
<title>tolvEn business card</title>
<link href="https://fonts.googleapis.com/css2?family=Open+Sans:wght@300;400&display=swap" rel="stylesheet">
<style>
  :root {
    --canvas-bg: #ecedee;
    --card-white: #ffffff;
    --brand-cyan: #12abe0;
    --brand-cyan-deep: #0393ce;
    --brand-green: #00a990;
    --brand-green-soft: #33b8a4;
    --text-dark: #2f3a3c;
    --rule-grey: #6f7f80;
    --faint-blue: #bfe3f3;
  }
  * { box-sizing: border-box; margin: 0; padding: 0; }
  html, body { width: 1200px; height: 892px; overflow: hidden; }
  body {
    background: var(--canvas-bg);
    font-family: "Open Sans", Arial, sans-serif;
    position: relative;
  }
  .card {
    position: absolute;
    top: 286px;
    width: 540px;
    height: 320px;
    background: var(--card-white);
    border-radius: 18px;
    overflow: hidden;
    box-shadow: 0 4px 16px rgba(0,0,0,0.12);
  }
  .card--front { left: 40px; }
  .card--back { left: 620px; }

  .faint-mark {
    position: absolute;
    border-radius: 50%;
    background: radial-gradient(circle, rgba(191,227,243,0) 48%, var(--faint-blue) 52%, var(--faint-blue) 60%, rgba(191,227,243,0) 64%);
    opacity: 0.8;
  }
  .card--front .faint-mark { width: 300px; height: 300px; right: -110px; top: -120px; }
  .card--back .faint-mark { width: 320px; height: 320px; right: -70px; bottom: -215px; }

  .brand {
    position: absolute;
    display: flex;
    align-items: center;
    gap: 12px;
  }
  .brand__dot {
    border: 4px solid var(--brand-green);
    border-radius: 50%;
  }
  .brand__name {
    font-weight: 400;
    color: var(--brand-cyan);
    letter-spacing: 1px;
  }
  .card--front .brand { left: 34px; top: 30px; }
  .card--front .brand__dot { width: 40px; height: 40px; }
  .card--front .brand__name { font-size: 50px; line-height: 1; }

  .person { position: absolute; left: 36px; top: 104px; }
  .person__name { font-size: 25px; font-weight: 400; color: var(--brand-cyan); line-height: 1.15; }
  .person__title { font-size: 17px; font-weight: 400; color: var(--text-dark); }

  .contact-list {
    position: absolute;
    left: 36px;
    top: 170px;
    list-style: none;
    font-size: 14.5px;
    color: var(--text-dark);
  }
  .contact-list li { display: flex; align-items: center; gap: 10px; height: 20px; }
  .contact-list svg { width: 15px; height: 15px; flex: none; }

  .band-rule {
    position: absolute; left: 0; right: 0; bottom: 56px;
    height: 2px; background: var(--brand-green);
  }
  .band {
    position: absolute; left: 0; right: 0; bottom: 0; height: 52px;
    background: linear-gradient(180deg, var(--brand-cyan) 0%, var(--brand-cyan-deep) 100%);
    display: flex;
    align-items: center;
    padding-left: 36px;
  }
  .band__tagline {
    font-size: 15px;
    font-weight: 400;
    color: var(--card-white);
    letter-spacing: 0.5px;
  }

  .card--back .brand { left: 150px; top: 100px; }
  .card--back .brand__dot { width: 52px; height: 52px; }
  .card--back .brand__name { font-size: 66px; line-height: 1; }
  .back-tagline {
    position: absolute;
    left: 0; right: 0;
    top: 192px;
    text-align: center;
    font-size: 16px;
    font-weight: 400;
    color: var(--brand-green);
    letter-spacing: 0.4px;
  }
</style>
</head>
<body>

  <section class="card card--front" aria-label="Business card front">
    <div class="faint-mark" role="img" aria-label="Faint large brand symbol decoration"></div>

    <div class="brand">
      <span class="brand__dot"></span>
      <span class="brand__name">tolvEn</span>
    </div>

    <div class="person">
      <p class="person__name">Rosalind Mercer</p>
      <p class="person__title">Chief Executive</p>
    </div>

    <ul class="contact-list">
      <li>
        <svg viewBox="0 0 15 15" aria-hidden="true"><rect width="15" height="15" rx="2" fill="#12abe0"/><circle cx="7.5" cy="7.5" r="4" fill="none" stroke="#fff" stroke-width="1.2"/><path d="M3.5 7.5h8M7.5 3.5v8" stroke="#fff" stroke-width="1"/></svg>
        www.tolven-example.com
      </li>
      <li>
        <svg viewBox="0 0 15 15" aria-hidden="true"><rect width="15" height="15" rx="2" fill="#12abe0"/><rect x="5" y="3" width="5" height="9" rx="1" fill="none" stroke="#fff" stroke-width="1.2"/></svg>
        +61 (0)438 516 702
      </li>
      <li>
        <svg viewBox="0 0 15 15" aria-hidden="true"><rect width="15" height="15" rx="2" fill="#12abe0"/><path d="M4 4c0 4 3 7 7 7l1-2-2-1-1 1c-1-.5-2-1.5-2.5-2.5l1-1-1-2z" fill="#fff"/></svg>
        +61 (0)2 8134 2907
      </li>
      <li>
        <svg viewBox="0 0 15 15" aria-hidden="true"><rect width="15" height="15" rx="2" fill="#12abe0"/><rect x="3" y="4.5" width="9" height="6" fill="none" stroke="#fff" stroke-width="1.1"/><path d="M3 4.5l4.5 3.5 4.5-3.5" fill="none" stroke="#fff" stroke-width="1.1"/></svg>
        rosalind.mercer@tolven-example.com
      </li>
    </ul>

    <div class="band-rule"></div>
    <div class="band">
      <p class="band__tagline">Mobile Travel Management</p>
    </div>
  </section>

  <section class="card card--back" aria-label="Business card back">
    <div class="faint-mark" role="img" aria-label="Faint large brand symbol decoration"></div>
    <div class="brand">
      <span class="brand__dot"></span>
      <span class="brand__name">tolvEn</span>
    </div>
    <p class="back-tagline">Accelerating Travel Business Insights</p>
  </section>

</body>
</html>
```